Business Card for Fashion House

We need a business card design for our personalize fashion service for our customers. the business card should reflect reliability, luxury and creativity.
The brand Gravetto is extracted from "Graceful Velvetto"; Gravetto provides fashion designs sprinkled with luxury and style tailored for our elite clients character profile.
Gravetto is created for those who embody class and elegance with a passion for style.
Target Market(s)
Affluent Customers
Industry/Entity Type
Fashion
Contact Information for Business Card
Samira Haddadin
Fashion Designer
Telephone: +971 4 555 0192
Mobile +971 50 555 0147
Emal info@gravetto-example.com
Website www.gravetto-example.com
Social Media Youtube g+ Facebook Instagram Pin /gravetto
Font styles to use
Other font styles liked:
- Audrey provided
Look and feel
Each slider illustrates characteristics of the customer's brand and the style your logo design should communicate.

```html
<!DOCTYPE html>
<html lang="en">
<head>
<meta charset="utf-8">
<title>Gravetto Business Card</title>
<link rel="stylesheet" href="https://fonts.googleapis.com/css2?family=Cormorant+Garamond:wght@400;600;700&display=swap">
<style>
  :root {
    --stage: #2b2b2e;
    --ink: #111111;
    --paper: #ffffff;
    --card-dark: #050505;
    --line-soft: #8a8a8a;
    --text-dark: #1a1a1a;
    --text-light: #f2f2f2;
  }
  * { box-sizing: border-box; margin: 0; padding: 0; }
  html, body {
    width: 1200px; height: 800px; overflow: hidden;
    background: var(--stage);
    font-family: "Cormorant Garamond", Georgia, serif;
  }
  .stage {
    width: 1200px; height: 800px;
    display: flex; align-items: center; justify-content: center; gap: 40px;
  }
  .card {
    width: 540px; height: 309px;
    position: relative;
    box-shadow: 0 14px 30px rgba(0,0,0,.45);
  }
  /* Front */
  .card--front {
    background: var(--card-dark);
    color: var(--text-light);
    display: flex; flex-direction: column; align-items: center; justify-content: center;
  }
  .brand-mark {
    width: 52px; height: 52px; border-radius: 50%;
    border: 3px solid currentColor;
  }
  .wordmark {
    font-weight: 400; font-size: 30px; letter-spacing: 0.42em;
    margin-right: -0.42em; text-transform: uppercase;
  }
  .card--front .wordmark { margin-top: 22px; }
  .social-row { display: flex; gap: 9px; margin-top: 20px; }
  .social-dot {
    width: 26px; height: 26px; border-radius: 50%;
    border: 2px solid var(--text-light);
  }
  /* Back */
  .card--back {
    background: var(--paper);
    color: var(--text-dark);
    display: flex; align-items: center;
  }
  .back-brand {
    width: 250px;
    display: flex; flex-direction: column; align-items: center;
  }
  .back-brand .wordmark { margin-top: 20px; font-size: 28px; }
  .divider {
    width: 1px; height: 150px; background: var(--line-soft);
  }
  .contact { padding-left: 26px; }
  .contact__name { font-weight: 700; font-size: 21px; line-height: 1; }
  .contact__role { font-size: 15px; margin-top: 2px; }
  .contact__list { list-style: none; margin-top: 18px; }
  .contact__item {
    display: flex; align-items: center; gap: 8px;
    font-size: 15px; line-height: 1.55;
  }
  .contact__icon {
    width: 16px; height: 16px; flex: none;
  }
</style>
</head>
<body>
<main class="stage">
  <section class="card card--front" aria-label="Card front">
    <div class="brand-mark" aria-hidden="true"></div>
    <p class="wordmark">Gravetto</p>
    <div class="social-row" aria-label="Social profiles /gravetto">
      <span class="social-dot"></span>
      <span class="social-dot"></span>
      <span class="social-dot"></span>
      <span class="social-dot"></span>
      <span class="social-dot"></span>
    </div>
  </section>

  <section class="card card--back" aria-label="Card back">
    <div class="back-brand">
      <div class="brand-mark" aria-hidden="true"></div>
      <p class="wordmark">Gravetto</p>
    </div>
    <div class="divider"></div>
    <div class="contact">
      <p class="contact__name">Samira Haddadin</p>
      <p class="contact__role">Fashion Designer</p>
      <ul class="contact__list">
        <li class="contact__item">
          <svg class="contact__icon" viewBox="0 0 16 16"><circle cx="8" cy="8" r="7.3" fill="none" stroke="#1a1a1a" stroke-width="1.2"/><path d="M5.2 4.3l1.4 0 .7 1.8-.9.8c.5 1 1.2 1.7 2.2 2.2l.8-.9 1.8.7v1.4c-3.4.2-6.2-2.6-6-6z" fill="#1a1a1a"/></svg>
          <span>+971 4 555 0192</span>
        </li>
        <li class="contact__item">
          <svg class="contact__icon" viewBox="0 0 16 16"><circle cx="8" cy="8" r="7.3" fill="none" stroke="#1a1a1a" stroke-width="1.2"/><rect x="5.5" y="3.8" width="5" height="8.4" rx="1" fill="none" stroke="#1a1a1a" stroke-width="1.1"/></svg>
          <span>+971 50 555 0147</span>
        </li>
        <li class="contact__item">
          <svg class="contact__icon" viewBox="0 0 16 16"><circle cx="8" cy="8" r="7.3" fill="none" stroke="#1a1a1a" stroke-width="1.2"/><rect x="4.3" y="5.3" width="7.4" height="5.4" fill="none" stroke="#1a1a1a" stroke-width="1.1"/><path d="M4.3 5.3L8 8.4l3.7-3.1" fill="none" stroke="#1a1a1a" stroke-width="1.1"/></svg>
          <span>info@gravetto-example.com</span>
        </li>
        <li class="contact__item">
          <svg class="contact__icon" viewBox="0 0 16 16"><circle cx="8" cy="8" r="7.3" fill="none" stroke="#1a1a1a" stroke-width="1.2"/><circle cx="8" cy="8" r="4.2" fill="none" stroke="#1a1a1a" stroke-width="1"/><ellipse cx="8" cy="8" rx="1.8" ry="4.2" fill="none" stroke="#1a1a1a" stroke-width="1"/><path d="M3.8 8h8.4" stroke="#1a1a1a" stroke-width="1"/></svg>
          <span>www.gravetto-example.com</span>
        </li>
      </ul>
    </div>
  </section>
</main>
</body>
</html>
```